TorbCutters Website & website development in Wordpress

Simple website for a 5 pages with some 15 products for sale.
We will sell T shirts and other Viking mens grooming products.

*****Lady barbers****
Also the company that gets awarded this job needs to be able to give me a quote to build the site in wordpress, just a design will not work.

Target Market(s)

The adventurous person likes to travels and get a good haircut

Coding

Coded - Design and coding required

Number of Pages Required

5+ page

Font styles to use
Sans Serif

Colors
3176b5
33a6d7

Requirements
Must have
• Must have a product order page for T-Shirts
Must have a travel adventure page with up to 5 recommended adventures
Must have a link to our instagram @torbcuttersformen page that would allow a client to book a haircut
Should show female stylists cutting mens hair- So far the only pictures in the designs submitted are male barbers
Nice to have
• We have this set up in GoDaddy would like to use wordpress. Thanks!

```html
<!DOCTYPE html>
<html lang="en">
<head>
<meta charset="utf-8">
<title>TorbCutters – Barber &amp; Grooming</title>
<link href="https://fonts.googleapis.com/css2?family=Poppins:wght@400;500;600;700&family=Roboto:wght@400;500;700&family=Great+Vibes&display=swap" rel="stylesheet">
<style>
:root{
  --blue:#3176b5;
  --sky:#33a6d7;
  --ink:#1d1d1f;
  --muted:#8a8a8a;
  --cream:#fffcf8;
  --white:#ffffff;
  --line:rgba(255,255,255,.35);
}
*{margin:0;padding:0;box-sizing:border-box}
html,body{width:1200px;height:4612px;overflow:hidden}
body{position:relative;background:var(--cream);font-family:Roboto,Arial,sans-serif;color:var(--ink)}
.abs{position:absolute}
.fill{position:absolute}
/* header / hero */
.hero{position:absolute;left:0;top:0;width:1200px;height:630px;background:linear-gradient(160deg,#5d7d98 0%,#3b5d78 35%,#2f8a8c 60%,#4a5a63 100%)}
.brand{position:absolute;left:108px;top:70px;display:flex;align-items:center;gap:8px;font-family:Poppins,sans-serif;font-weight:700;font-size:22px;color:var(--white)}
.brand-dot{width:22px;height:22px;border-radius:50%;background:#e0262b}
.topbar{position:absolute;top:21px;right:110px;display:flex;gap:36px;font-size:13px;color:var(--white)}
.topbar span{display:flex;align-items:center;gap:7px}
.nav{position:absolute;left:365px;top:72px;width:745px;border-bottom:1px solid var(--line);height:42px;display:flex;gap:30px;font-family:Poppins,sans-serif;font-size:14px;font-weight:500;color:var(--white)}
.nav a{color:inherit;text-decoration:none;padding-top:8px}
.nav a.active{color:var(--sky);border-bottom:2px solid var(--sky)}
.hero-title{position:absolute;left:109px;top:272px;font-family:Poppins,sans-serif;font-weight:700;font-size:37px;line-height:48px;color:var(--white);letter-spacing:.3px;text-transform:uppercase;white-space:nowrap}
.hero-text{position:absolute;left:109px;top:333px;width:510px;font-size:15px;line-height:25px;color:var(--white)}
.btn{position:absolute;display:flex;align-items:center;justify-content:center;gap:10px;background:var(--blue);color:var(--white);font-family:Roboto,sans-serif;font-weight:700;font-size:14px;text-transform:uppercase}
.btn i{font-style:normal;font-size:10px}
/* section headings */
.eyebrow{position:absolute;left:0;width:1200px;text-align:center;font-size:15px;color:var(--blue);font-weight:500}
.title{position:absolute;left:0;width:1200px;text-align:center;font-family:Poppins,sans-serif;font-weight:600;font-size:33px;color:var(--ink)}
/* services */
.service{position:absolute;top:835px;width:222px;text-align:center}
.service .photo{width:222px;height:222px;border-radius:50%;border:4px solid var(--blue);background:linear-gradient(180deg,#c9b8a6,#6d5a4c)}
.service .badge{position:absolute;left:71px;top:170px;width:80px;height:80px;border-radius:50%;background:var(--blue);border:4px solid var(--white);display:flex;align-items:center;justify-content:center}
.service h3{margin-top:50px;font-family:Roboto,sans-serif;font-size:16px;font-weight:500;color:var(--ink)}
/* about */
.about-img{left:0;top:1307px;width:600px;height:425px;background:linear-gradient(180deg,#3a3c44 0%,#7d8087 45%,#6e6258 100%)}
.about-box{position:absolute;left:600px;top:1232px;width:600px;height:423px;background:var(--blue);color:var(--white)}
.about-box .label{position:absolute;left:55px;top:92px;font-size:17px}
.about-box h2{position:absolute;left:55px;top:112px;font-family:Poppins,sans-serif;font-size:34px;font-weight:600}
.about-box p{position:absolute;left:55px;top:172px;width:425px;font-size:13px;line-height:24.3px}
/* products */
.card{position:absolute;width:229px;height:290px;background:var(--white);box-shadow:0 2px 8px rgba(0,0,0,.08);text-align:center}
.card .img{position:absolute;left:60px;top:16px;width:110px;height:131px;border-radius:6px}
.card h4{position:absolute;top:168px;left:0;width:100%;font-size:14px;font-weight:500;line-height:21px}
.card .price{position:absolute;top:212px;left:0;width:100%;font-size:12px;color:var(--muted)}
.card .price b{font-family:Poppins,sans-serif;font-size:16px;color:var(--blue);font-weight:600}
.card .btn{left:37px;top:242px;width:160px;height:32px;background:var(--sky);font-size:14px}
/* testimonials */
.testi{left:0;top:2699px;width:1200px;height:382px;background:linear-gradient(135deg,#2f8fcf 0%,#3aa3da 60%,#2b86c6 100%)}
.testi h2{position:absolute;left:0;top:60px;width:1200px;text-align:center;font-family:Poppins,sans-serif;font-weight:600;font-size:33px;color:var(--white)}
.quote{position:absolute;top:151px;width:500px;color:var(--white)}
.quote .avatar{position:absolute;left:0;top:0;width:163px;height:163px;border-radius:50%;background:linear-gradient(180deg,#e8e2da,#b99f88)}
.quote .qmark{position:absolute;left:52px;top:122px;width:56px;height:56px;border-radius:50%;background:var(--blue);display:flex;align-items:center;justify-content:center;font-family:Poppins,sans-serif;font-size:30px;font-weight:700;line-height:1;padding-top:14px}
.quote .stars{position:absolute;left:185px;top:16px;color:#f5c518;font-size:15px;letter-spacing:2px}
.quote p{position:absolute;left:185px;top:44px;width:290px;font-size:14px;font-style:italic;line-height:24px}
.quote .name{position:absolute;left:185px;top:128px;font-size:13px;font-weight:700}
/* offer */
.offer-img{left:596px;top:3081px;width:604px;height:440px;background:linear-gradient(180deg,#c8d3da 0%,#8a9a6a 55%,#5b6d3c 100%)}
.script{position:absolute;left:113px;top:3138px;font-family:"Great Vibes",cursive;font-size:40px;color:var(--blue)}
.offer-text{position:absolute;left:113px;top:3205px;width:400px;font-size:14px;line-height:25px;color:var(--muted)}
.offer-head{position:absolute;left:113px;top:3278px;font-family:Poppins,sans-serif;font-weight:600;font-size:23px;color:var(--ink)}
.pct{position:absolute;left:113px;top:3320px;font-family:Poppins,sans-serif;font-weight:600;font-size:42px;color:var(--sky)}
.pct-note{position:absolute;left:222px;top:3330px;font-family:Poppins,sans-serif;font-size:17px;line-height:25px;color:var(--ink)}
/* contact */
.contact{position:absolute;top:3670px;display:flex;gap:14px}
.contact .ico{width:68px;height:68px;border-radius:50%;border:2px solid var(--blue);display:flex;align-items:center;justify-content:center}
.contact .ico span{width:50px;height:50px;border-radius:50%;background:var(--blue);display:flex;align-items:center;justify-content:center}
.contact h5{font-size:14px;font-weight:700;margin-top:4px}
.contact p{font-size:13px;color:var(--muted);line-height:22px;margin-top:6px}
.pattern{left:0;top:3788px;width:1200px;height:59px;background:linear-gradient(180deg,#f1f1f1,#d9d9d9)}
.map{left:0;top:3847px;width:1200px;height:348px;background:linear-gradient(120deg,#dfe6dd 0%,#e6e6e3 45%,#e0e3e8 100%)}
.lower{left:0;top:4195px;width:1200px;height:417px;background:linear-gradient(180deg,#b9c2cc 0%,#dfe3e7 50%,#c7cbcf 100%)}
.inquiry{position:absolute;left:183px;top:4096px;width:834px;height:405px;background:linear-gradient(180deg,#3b74b0,#2f6aaa);color:var(--white)}
.inquiry h3{position:absolute;left:48px;top:172px;font-family:Poppins,sans-serif;font-size:28px;font-weight:600;line-height:38px}
.field{position:absolute;font-size:12px;border-bottom:1px solid var(--line);height:30px}
.submit{position:absolute;left:240px;top:281px;width:571px;height:41px;background:var(--sky);display:flex;align-items:center;justify-content:center;font-size:13px;font-weight:700}
.footer{position:absolute;left:181px;top:4554px;font-size:13px;color:var(--ink)}
.social{position:absolute;left:842px;top:4544px;display:flex;gap:9px}
.social span{width:38px;height:38px;border-radius:50%;border:2px solid var(--ink)}
</style>
</head>
<body>

<header class="hero" role="img" aria-label="Hiker with backpack sitting on a cliff above a turquoise fjord"></header>
<div class="brand"><span class="brand-dot"></span>TorbCutters</div>
<div class="topbar">
  <span><svg width="12" height="12" viewBox="0 0 24 24" fill="#fff"><path d="M6.6 10.8a15.1 15.1 0 006.6 6.6l2.2-2.2a1 1 0 011-.25 11.4 11.4 0 003.6.6 1 1 0 011 1V20a1 1 0 01-1 1A17 17 0 013 4a1 1 0 011-1h3.5a1 1 0 011 1c0 1.25.2 2.45.6 3.6a1 1 0 01-.25 1z"/></svg>555-218-4490</span>
  <span><svg width="13" height="12" viewBox="0 0 24 24" fill="#fff"><path d="M2 5h20v14H2z" opacity=".9"/><path d="M2 5l10 8 10-8" stroke="#3b5d78" stroke-width="2" fill="none"/></svg>hello@torbcutters.com</span>
</div>
<nav class="nav">
  <a class="active" href="#">Home</a><a href="#">About</a><a href="#">Services</a><a href="#">Products</a><a href="#">Product Order</a><a href="#">Blog</a><a href="#">Travel adventure</a><a href="#">Contact</a>
</nav>
<h1 class="hero-title">Take care of your cair</h1>
<p class="hero-text">Lorem ipsum dolor sit amet, consectetur adipiscing elit, sed do eiusmod tempor incididunt ut magna aliqua.</p>
<div class="btn" style="left:109px;top:414px;width:177px;height:46px">View Offer <i>▶</i></div>
<svg class="abs" style="left:0;top:310px" width="28" height="44" viewBox="0 0 28 44"><path d="M0 0h6l22 22-22 22H0z" fill="#3176b5"/><path d="M14 16l-6 6 6 6" stroke="#fff" stroke-width="2" fill="none"/></svg>
<svg class="abs" style="left:1172px;top:310px" width="28" height="44" viewBox="0 0 28 44"><path d="M28 0h-6L0 22l22 22h6z" fill="#3176b5"/><path d="M14 16l6 6-6 6" stroke="#fff" stroke-width="2" fill="none"/></svg>

<div class="eyebrow" style="top:722px">Professional Service</div>
<h2 class="title" style="top:742px">Thisis What You Get</h2>
<div class="service" style="left:113px"><div class="photo" role="img" aria-label="Young man in sunglasses with a classic cut"></div><div class="badge"><svg width="34" height="34" viewBox="0 0 24 24" fill="none" stroke="#fff" stroke-width="2"><circle cx="6" cy="6" r="3"/><circle cx="6" cy="18" r="3"/><path d="M8.5 7.5L20 18M8.5 16.5L20 6"/></svg></div><h3>CLASSIC CUTS</h3></div>
<div class="service" style="left:364px"><div class="photo" role="img" aria-label="Smiling man touching his freshly groomed face"></div><div class="badge"><svg width="34" height="34" viewBox="0 0 24 24" fill="none" stroke="#fff" stroke-width="2"><path d="M4 20L16 8l4-4M14 6l4 4"/></svg></div><h3>GROOMING</h3></div>
<div class="service" style="left:613px"><div class="photo" role="img" aria-label="Man having hair coloured at the salon"></div><div class="badge"><svg width="34" height="34" viewBox="0 0 24 24" fill="none" stroke="#fff" stroke-width="2"><path d="M12 3c4 5 6 8 6 11a6 6 0 01-12 0c0-3 2-6 6-11z"/></svg></div><h3>COLOR SERVICES</h3></div>
<div class="service" style="left:863px"><div class="photo" role="img" aria-label="Bearded man receiving a beard trim"></div><div class="badge"><svg width="34" height="34" viewBox="0 0 24 24" fill="none" stroke="#fff" stroke-width="2"><rect x="4" y="10" width="16" height="10" rx="1"/><path d="M7 10V6M11 10V5M15 10V6"/></svg></div><h3>WAX SERVICES</h3></div>

<div class="fill about-img" role="img" aria-label="Interior of the barbershop with rows of barber chairs"></div>
<section class="about-box">
  <span class="abs" style="left:55px;top:32px;width:24px;height:24px;border-radius:50%;background:#e0262b"></span>
  <div class="label">About Us</div>
  <h2>TorbCutters</h2>
  <p>Lorem ipsum dolor sit amet, consectetur adipiscing elit, sed do eiusmod tempor incididunt ut labore et dolore magna aliqua. Ut enim ad minim veniam, quis nostrud exercitation ullamco laboris nisi ut aliquip ex ea commodo consequat. Duis aute irure dolor in reprehenderit in voluptate velit esse cillum dolore eu fugiat nulla pariatur.</p>
  <div class="btn" style="left:55px;top:344px;width:142px;height:41px;background:var(--sky)">Read More <i>●</i></div>
</section>

<div class="eyebrow" style="top:1829px">Top Quality</div>
<h2 class="title" style="top:1853px">Hair &amp; Care Products</h2>

<div class="card" style="left:111px;top:1945px"><div class="img" role="img" aria-label="Dark grooming cream tube" style="background:linear-gradient(90deg,#4a555b,#748088)"></div><h4>Lorem ipsum dolor amet,<br>consectetur</h4><div class="price">From <b>$20.35</b></div><div class="btn">Know More <i>▶</i></div></div>
<div class="card" style="left:360px;top:1945px"><div class="img" role="img" aria-label="Royal blue T-shirt" style="background:#1e3fbf"></div><h4>Lorem ipsum dolor amet,<br>consectetur</h4><div class="price">From <b>$20.35</b></div><div class="btn">Know More <i>▶</i></div></div>
<div class="card" style="left:608px;top:1945px"><div class="img" role="img" aria-label="White spray bottle" style="background:linear-gradient(90deg,#d8d8d8,#f4f4f4)"></div><h4>Lorem ipsum dolor amet,<br>consectetur</h4><div class="price">From <b>$20.35</b></div><div class="btn">Know More <i>▶</i></div></div>
<div class="card" style="left:857px;top:1945px"><div class="img" role="img" aria-label="Grey T-shirt" style="background:#8c8c8c"></div><h4>Lorem ipsum dolor amet,<br>consectetur</h4><div class="price">From <b>$20.35</b></div><div class="btn">Know More <i>▶</i></div></div>

<div class="card" style="left:111px;top:2264px"><div class="img" role="img" aria-label="Black T-shirt" style="background:#151515"></div><h4>Lorem ipsum dolor amet,<br>consectetur</h4><div class="price">From <b>$20.35</b></div><div class="btn">Know More <i>▶</i></div></div>
<div class="card" style="left:360px;top:2264px"><div class="img" role="img" aria-label="Electric shaver" style="background:linear-gradient(90deg,#222,#6b6b6b)"></div><h4>Lorem ipsum dolor amet,<br>consectetur</h4><div class="price">From <b>$20.35</b></div><div class="btn">Know More <i>▶</i></div></div>
<div class="card" style="left:608px;top:2264px"><div class="img" role="img" aria-label="Light blue T-shirt" style="background:#a9cff0"></div><h4>Lorem ipsum dolor amet,<br>consectetur</h4><div class="price">From <b>$20.35</b></div><div class="btn">Know More <i>▶</i></div></div>
<div class="card" style="left:857px;top:2264px"><div class="img" role="img" aria-label="White lotion bottle" style="background:linear-gradient(90deg,#dcdcdc,#f6f6f6)"></div><h4>Lorem ipsum dolor amet,<br>consectetur</h4><div class="price">From <b>$20.35</b></div><div class="btn">Know More <i>▶</i></div></div>

<section class="fill testi">
  <h2>What our Client Says</h2>
  <div class="quote" style="left:111px">
    <div class="avatar" role="img" aria-label="Portrait of a smiling client"></div>
    <div class="qmark">”</div>
    <div class="stars">★★★★★</div>
    <p>"Lorem ipsum dolor sit amet, consectetur adip is cing elit, sed do eiusmod tempor incididunt ut labore et dolore magna</p>
    <div class="name">John Doe</div>
  </div>
  <div class="quote" style="left:618px">
    <div class="avatar" role="img" aria-label="Portrait of a second client"></div>
    <div class="qmark">”</div>
    <div class="stars">★★★★★</div>
    <p>"Lorem ipsum dolor sit amet, consectetur adip is cing elit, sed do eiusmod tempor incididunt ut labore et dolore magna</p>
    <div class="name">John Doe</div>
  </div>
</section>

<div class="script">Special Offer</div>
<p class="offer-text">Lorem ipsum dolor sit amet, consectetur adipiscing elit, sed do eiusmod tempor</p>
<div class="offer-head">NOW OFFERING</div>
<div class="pct">10%</div>
<div class="pct-note">Discount For<br>Students</div>
<div class="btn" style="left:116px;top:3412px;width:162px;height:45px">Know More <i>●</i></div>
<div class="fill offer-img" role="img" aria-label="Man with arms outstretched on a mountain top"></div>

<h2 class="title" style="top:3604px">Contact Us</h2>
<div class="contact" style="left:183px"><div class="ico"><span><svg width="20" height="24" viewBox="0 0 24 24" fill="#fff"><path d="M12 2a7 7 0 00-7 7c0 5 7 13 7 13s7-8 7-13a7 7 0 00-7-7zm0 9.5A2.5 2.5 0 1112 6a2.5 2.5 0 010 5.5z"/></svg></span></div><div><h5>Address:</h5><p>123, Lorem ipsum dolor sit amet,<br>consectetur adipiscing</p></div></div>
<div class="contact" style="left:505px"><div class="ico"><span><svg width="20" height="20" viewBox="0 0 24 24" fill="#fff"><path d="M6.6 10.8a15.1 15.1 0 006.6 6.6l2.2-2.2a1 1 0 011-.25 11.4 11.4 0 003.6.6 1 1 0 011 1V20a1 1 0 01-1 1A17 17 0 013 4a1 1 0 011-1h3.5a1 1 0 011 1c0 1.25.2 2.45.6 3.6a1 1 0 01-.25 1z"/></svg></span></div><div><h5 style="margin-top:14px">Phone</h5><p>(888) 888-8888</p></div></div>
<div class="contact" style="left:754px"><div class="ico"><span><svg width="22" height="18" viewBox="0 0 24 20" fill="none" stroke="#fff" stroke-width="2"><rect x="2" y="2" width="20" height="16" rx="1"/><path d="M2 3l10 8 10-8"/></svg></span></div><div><h5 style="margin-top:14px">Email:</h5><p>info@torbcutters.com</p></div></div>

<div class="fill pattern" role="img" aria-label="Decorative band of barber tools"></div>
<div class="fill map" role="img" aria-label="Street map showing the shop location"></div>
<div class="fill lower" role="img" aria-label="Snowy mountain landscape"></div>

<section class="inquiry">
  <svg class="abs" style="left:48px;top:88px" width="88" height="60" viewBox="0 0 88 60" fill="none" stroke="#fff" stroke-width="3"><rect x="2" y="2" width="84" height="56"/><path d="M2 2l42 32L86 2M2 58l30-28M86 58L56 30"/></svg>
  <h3>QUICK<br>INQUIRY</h3>
  <div class="field" style="left:249px;top:82px;width:294px">First Name*</div>
  <div class="field" style="left:551px;top:82px;width:260px">Last Name*</div>
  <div class="field" style="left:249px;top:149px;width:294px">Your Phone*</div>
  <div class="field" style="left:551px;top:149px;width:260px">Your Email*</div>
  <div class="field" style="left:249px;top:208px;width:562px;height:42px">Message*</div>
  <div class="submit">SUBMIT</div>
</section>

<div class="footer">Copyright 2021 TorbCutters | All Rights Reserved.</div>
<div class="social"><span></span><span></span><span></span><span></span></div>

</body>
</html>
```